International Business Development Firm, in need of Branded Stationery material

We just made our Logo and now we are looking for branded stationery for our company such as:

* A Letterhead with our company's name, address, and logo at the top in Word format for easy editing
* A more formal letter format with a light background design (watermark) featuring our logo, allowing us to write over it for various documents and presentations
* Business card + Envelopes are a plus but not a must
* PowerPoint for company and product introductions
* An Info sheet with Bullet Points

The design should be professional.
Please ensure the design is high quality and print ready.

Target Market(s)

Businesses and high net value individuels

Industry/Entity Type

International Business Development Firm

Colors

Designer to choose colors to be used in the design.

Requirements
Must have
• word docs so i can use the stationery templates afterwards

```html
<!DOCTYPE html>
<html lang="en">
<head>
<meta charset="utf-8">
<title>Halvora Capital – Stationery</title>
<link href="https://fonts.googleapis.com/css2?family=Lato:wght@400;700&family=Open+Sans:wght@400;600&family=Dancing+Script:wght@500&display=swap" rel="stylesheet">
<style>
:root{
  --brand:#5b3a8c;
  --brand-soft:#8f73b8;
  --ink:#1e1e1e;
  --paper:#ffffff;
  --canvas:#ffffff;
  --edge:#e2e2e6;
  --watermark:#f5f3f9;
}
*{box-sizing:border-box;margin:0;padding:0}
html,body{width:1200px;height:824px;overflow:hidden;background:var(--canvas)}
body{position:relative;font-family:"Lato",sans-serif;color:var(--ink)}
.sheet{position:absolute;background:var(--paper);border:1px solid var(--edge)}

.brand{display:flex;align-items:center;gap:6px;color:var(--brand);font-family:"Lato",sans-serif;font-weight:700;letter-spacing:.04em;white-space:nowrap}
.brand-dot{border-radius:50%;background:var(--brand);flex:none}

/* letterhead */
.letterhead{left:127px;top:101px;width:442px;height:624px;overflow:hidden}
.letterhead .watermark{position:absolute;left:121px;top:190px;width:200px;height:200px;border-radius:50%;background:var(--watermark)}
.letterhead .brand{position:absolute;left:22px;top:40px;font-size:20px}
.letterhead .brand-dot{width:16px;height:16px}
.contact{position:absolute;left:313px;top:26px;border-left:1px solid var(--brand);padding-left:11px;font-family:"Open Sans",sans-serif;font-size:8.4px;line-height:10px;color:#333}
.contact .addr{margin-bottom:5px}
.contact li{list-style:none;display:flex;align-items:center;gap:4px}
.icon{width:6px;height:6px;flex:none}
.letter{position:absolute;left:22px;top:143px;width:398px;font-size:9px;line-height:10px}
.letter p{margin-bottom:10.5px}
.letter .greeting{font-weight:700;font-size:11.5px;margin:1px 0 10px}
.letter .body{text-align:justify;margin-bottom:9.5px}
.letter .regards{margin-top:22px}
.signature{font-family:"Dancing Script",cursive;font-size:20px;margin-top:40px;display:block}

/* business cards */
.card{top:101px;width:212px;height:120px;border-radius:8px}
.card-front{left:633px}
.card-front .brand{position:absolute;left:22px;top:53px;font-size:9px;gap:4px}
.card-front .brand-dot{width:8px;height:8px}
.card-front .details{position:absolute;left:110px;top:30px;height:61px;border-left:1px solid var(--brand);padding-left:10px;font-family:"Open Sans",sans-serif;font-size:5.6px;line-height:7.6px;color:#333}
.card-front .name{font-family:"Lato",sans-serif;font-weight:700;color:var(--brand);font-size:8.6px;line-height:9px}
.card-front .role{color:var(--brand-soft);font-size:5.4px;margin-bottom:3px}
.card-front li{list-style:none;display:flex;align-items:center;gap:3px}
.card-front .icon{width:4px;height:4px}
.card-front .addr{margin-top:3px}
.card-back{left:862px}
.card-back .brand{position:absolute;left:0;right:0;top:48px;justify-content:center;font-size:17px}
.card-back .brand-dot{width:14px;height:14px}

/* envelope back */
.envelope-back{left:623px;top:277px;width:451px;height:198px}
.flap{position:absolute;left:-1px;right:-1px;top:-1px;height:60px;border:1px solid var(--edge);border-top:none;border-radius:0 0 30px 30px;background:var(--paper)}
.flap .brand-dot{position:absolute;left:218px;top:23px;width:15px;height:15px}

/* envelope front */
.envelope-front{left:623px;top:530px;width:451px;height:195px}
.envelope-front .brand{position:absolute;left:23px;top:35px;font-size:18px}
.envelope-front .brand-dot{width:15px;height:15px}
.envelope-front .addr{position:absolute;left:40px;width:120px;top:70px;text-align:center;font-family:"Open Sans",sans-serif;font-size:7.4px;line-height:10.5px;color:#333}
.envelope-front .window{position:absolute;left:23px;top:130px;width:92px;height:36px;background:linear-gradient(125deg,#dadada 0%,#e6e6e6 40%,#9a9a9a 55%,#efefed 70%,#f0f0ee 100%)}
</style>
</head>
<body>

<svg width="0" height="0" style="position:absolute" aria-hidden="true">
  <symbol id="i-phone" viewBox="0 0 10 10"><path d="M2 1l2 2-1 1.3a6 6 0 0 0 2.7 2.7L7 6l2 2-1.2 1.3C4.5 9.5.5 5.5.7 2.2z" fill="#5b3a8c"/></symbol>
  <symbol id="i-mail" viewBox="0 0 10 10"><rect x="1" y="2.5" width="8" height="5.5" rx=".6" fill="#5b3a8c"/><path d="M1.4 3l3.6 2.6L8.6 3" stroke="#fff" stroke-width=".8" fill="none"/></symbol>
  <symbol id="i-web" viewBox="0 0 10 10"><circle cx="5" cy="5" r="4" fill="#5b3a8c"/><path d="M1 5h8M5 1c-2 2.5-2 5.5 0 8M5 1c2 2.5 2 5.5 0 8" stroke="#fff" stroke-width=".6" fill="none"/></symbol>
</svg>

<section class="sheet letterhead">
  <div class="watermark" aria-hidden="true"></div>
  <div class="brand"><span class="brand-dot"></span>HALVORA CAPITAL</div>
  <div class="contact">
    <div class="addr">Your address, City<br>State, Zip 1234</div>
    <ul>
      <li><svg class="icon"><use href="#i-phone"/></svg>123 456 789</li>
      <li><svg class="icon"><use href="#i-mail"/></svg>info@yourgmail.com</li>
      <li><svg class="icon"><use href="#i-web"/></svg>www.yourwebsite.com</li>
    </ul>
  </div>
  <div class="letter">
    <p>January-03-2020</p>
    <p>Mr, Peter Lang<br>President</p>
    <p>Northway Group<br>123 Street Name, Suite# 10<br>City, State, 120023</p>
    <p class="greeting">Dear Mr, Peter</p>
    <p class="body">Lorem ipsum dolor sit amet, consectetur adipiscing elit, sed do eiusmod tempor incididunt ut labore et dolore magna aliqua. Ut enim ad minim veniam, quis nostrud exercitation ullamco laboris nisi ut aliquip ex ea commodo consequat. Duis aute irure dolor in reprehenderit in voluptate velit esse cillum dolore eu fugiat nulla pariatur.</p>
    <p class="body">Lorem ipsum dolor sit amet, consectetur adipiscing elit, sed do eiusmod tempor incididunt ut labore et dolore magna aliqua. Ut enim ad minim veniam, quis nostrud exercitation ullamco laboris nisi ut aliquip ex ea commodo consequat. Duis aute irure dolor in reprehenderit in voluptate velit esse cillum dolore eu fugiat nulla pariatur.</p>
    <p class="body">Lorem ipsum dolor sit amet, consectetur adipiscing elit, sed do eiusmod tempor incididunt ut labore et dolore magna aliqua. Ut enim ad minim veniam, quis nostrud exercitation ullamco laboris nisi ut aliquip ex ea commodo consequat.</p>
    <p class="body">Excepteur sint occaecat cupidatat non proident, sunt in culpa qui officia deserunt mollit anim id est laborum. re et dolore magnam aliquam quaerat voluptatem.</p>
    <p class="regards">Regards</p>
    <span class="signature">Laura Finch</span>
  </div>
</section>

<section class="sheet card card-front">
  <div class="brand"><span class="brand-dot"></span>HALVORA CAPITAL</div>
  <div class="details">
    <div class="name">DANIEL REYES</div>
    <div class="role">MANAGING DIRECTOR</div>
    <ul>
      <li><svg class="icon"><use href="#i-phone"/></svg>123 456 789</li>
      <li><svg class="icon"><use href="#i-mail"/></svg>info@yourgmail.com</li>
      <li><svg class="icon"><use href="#i-web"/></svg>www.yourwebsite.com</li>
    </ul>
    <div class="addr">Your address, City<br>State, Zip 1234</div>
  </div>
</section>

<section class="sheet card card-back">
  <div class="brand"><span class="brand-dot"></span>HALVORA CAPITAL</div>
</section>

<section class="sheet envelope-back">
  <div class="flap"><span class="brand-dot" aria-hidden="true"></span></div>
</section>

<section class="sheet envelope-front">
  <div class="brand"><span class="brand-dot"></span>HALVORA CAPITAL</div>
  <div class="addr">Your address, City<br>State, Zip 1234</div>
  <div class="window" aria-hidden="true"></div>
</section>

</body>
</html>
```